Letterhead Design for Law Firm

**Edit: I have added the photo of a bottom that I like.

------
We are looking for a re-design of our new letterhead. The letterhead is for a law firm and will be used for digital and traditionally printed correspondence.

Here are some suggestions:

- Please use colours are #8ec900 and simple black.
- Please do not use any type of "waves" at the bottom of the page. This is not in style at all.
- Please stay modern yet conservative.
- Please use font Segoe UI Light or similar if you can
- Avoid clipart or illustrations.
- Utilize ample white space in the layout so the design looks clean and information is easy to read at a glance. Don't overcrowd the letterhead.
- Make sure the letterhead design is consistent with our brand identity (see corvelith.ca)
-Please, no black headers or footers.

I am attaching my current letterhead and signature for your convenience.

Remember, the letterhead is an extension of our professional identity. We are a successful firm and trial lawyers who correspond with insurers, judges, lawyers, courts, clients, etc. Make it new, modern, attractive, yet powerful and conservative.

It needs to be easily printable. I would like the bleed removed in print so the black bar the bottom crosses the page (but the text is not near the edges)
Updates

Low design quality

Target Market(s)

Clients, Government Offices, Judiciary, Lawyers, Insurance Companies, Colleagues.

Industry/Entity Type

Law

Other font styles liked:
• Segoe UI LIght, Calibri Light,

Colors
00AB8E
00BBA5
67D7C9
C6EFE9
E9F9F6

Requirements
Must have
• Everything that is on the letterhead now.
Nice to have
• Cutting Edge design, yet conservative.
Should not have
• law firm cliche design, images,

```html
<!DOCTYPE html>
<html lang="en">
<head>
<meta charset="utf-8">
<title>Corvelith Letterhead</title>
<link rel="stylesheet" href="https://fonts.googleapis.com/css2?family=Open+Sans:wght@300;400;600&display=swap">
<style>
  :root {
    --brand-green: #8ec900;
    --ink: #111111;
    --ink-soft: #2a2a2a;
    --paper: #ffffff;
    --backdrop: #c9c9c9;
    --placeholder: #e6e6e6;
  }
  * { margin: 0; padding: 0; box-sizing: border-box; }
  html, body {
    width: 1200px; height: 686px; overflow: hidden;
    background: var(--backdrop);
    font-family: "Open Sans", "Segoe UI", sans-serif;
    color: var(--ink);
  }
  .letterhead {
    position: absolute; left: 369px; top: 22px;
    width: 462px; height: 642px;
    background: var(--paper);
    box-shadow: 0 4px 18px rgba(0,0,0,0.18);
  }
  .brand { position: absolute; left: 40px; top: 44px; }
  .brand-name {
    font-size: 30px; font-weight: 400; letter-spacing: 1px; line-height: 1;
  }
  .brand-tagline {
    font-size: 7.5px; font-weight: 400; letter-spacing: 1.6px; margin-top: 5px;
  }
  .contact {
    position: absolute; left: 290px; top: 40px;
    border-left: 1px solid var(--brand-green);
    padding-left: 10px;
    font-size: 7px; font-weight: 300; line-height: 1.35; color: var(--ink-soft);
  }
  .contact .web-accent { color: var(--brand-green); }
  .contact .practice { margin-top: 7px; }
  .letter-meta {
    position: absolute; left: 58px; top: 116px;
    font-size: 8px; font-weight: 400; line-height: 1.4;
  }
  .letter-meta p { margin-bottom: 7px; }
  .recipient { margin-bottom: 10px; }
  .subject-row { display: flex; }
  .subject-label { width: 90px; }
  .subject-lines { font-size: 8px; }
  .subject-rule {
    position: absolute; left: 148px; top: 332px;
    width: 290px; height: 1px; background: var(--brand-green);
  }
  .sign-off {
    position: absolute; left: 158px; top: 488px;
    font-size: 8px; font-weight: 400; line-height: 1.4;
  }
  .signature-area {
    width: 130px; height: 36px; margin: 6px 0 4px;
    background: var(--placeholder);
  }
</style>
</head>
<body>
  <main class="letterhead">
    <header class="brand">
      <div class="brand-name">CORVELITH</div>
      <div class="brand-tagline">PERSONAL INJURY LAWYERS</div>
    </header>

    <aside class="contact">
      <div>www.<span class="web-accent">CORVELITH</span>.ca</div>
      <div>48 Harbour Street E., Suite 910</div>
      <div>Brantwell, ON&nbsp; K7R 3B2</div>
      <div>T: 555-214-7730</div>
      <div>F: 555-214-7731</div>
      <div>File Clerk: Nadia Forsythe</div>
      <div>Email: nadia@corvelith.ca</div>
      <div class="practice">Practice Restricted</div>
      <div>Serious Personal Injury</div>
      <div>Wrongful Death Litigation</div>
      <div>Long-Term Disability Litigation</div>
      <div>Wrongful Dismissal Litigation</div>
      <div>Employee Terminations</div>
    </aside>

    <section class="letter-meta">
      <p>Without Prejudice</p>
      <p>March 13, 2024</p>
      <p>By Email</p>
      <div class="recipient">
        Harrowgate Insurance Company<br>
        Claims Litigation Department<br>
        72 Elmcrest Road North<br>
        P.O. Box 4100<br>
        Linmoor, ON&nbsp;&nbsp; M3T 6P1
      </div>
      <p>Attention:&nbsp; Mr. Colin Marsh</p>
      <p>Mr. Marsh:</p>
      <div class="subject-row">
        <span class="subject-label">Re:</span>
        <span class="subject-lines">
          Varga v. Delmonte et al.<br>
          DOL:&nbsp; September 12, 2019<br>
          Pre-Mediation Settlement Proposal – March 13th, 2024
        </span>
      </div>
    </section>
    <div class="subject-rule"></div>

    <footer class="sign-off">
      <div>Yours very truly,</div>
      <div>CORVELITH PERSONAL INJURY LAWYERS</div>
      <div class="signature-area" role="img" aria-label="Handwritten signature of the signing lawyer"></div>
      <div>Marc R. Corvelith</div>
      <div>Corvelith Law Professional Corporation</div>
      <div>/nf</div>
      <div>Encl.</div>
    </footer>
  </main>
</body>
</html>
```